Laser Tattoo Removal Business Cards

We are looking for a professional business card design for a laser tattoo removal business. Ideally looking for a black business card design. The name of the business is Brightline Tattoo Removal. We place our cards at local tattoo shops so we ideally are looking for something trendy/edgy to draw both male and female clientele in.

Target Market(s)

Male/Female ages 18-60

Contact Information for Business Card

black background ideally.. hoping to stay within greys, whites and black

Font styles to use
Serif
Sans Serif

Colors
121212
a9a9a9
5c5c5c
f5f5f5
ffffff
7f7f7f
606060
848484
9d9d9d

Requirements
Must have
• Employee Info:
• Melissa Thornbury
• Chief Executive Offer
• m: 919.537.2846
• w: 919.362.4178
• f: 919.685.3907
• mthornbury@brightlinetattooremoval.example
• Address:
• 4615 Oakmere Pkwy, Suite 210
• Raleigh, NC 27654
• Website:
• www.brightlinetattooremoval.example
Nice to have
• Myabe business name on back or logo on back and employee info on the front

```html
<!DOCTYPE html>
<html lang="en">
<head>
<meta charset="utf-8">
<title>Brightline Tattoo Removal — Business Cards</title>
<link rel="stylesheet" href="https://fonts.googleapis.com/css2?family=Roboto:wght@400;500;700&display=swap">
<style>
  :root {
    --stage: #3a3633;
    --card: #121212;
    --ink: #ffffff;
    --ink-soft: #f5f5f5;
    --rule: #f5f5f5;
    --muted: #a9a9a9;
  }
  * { box-sizing: border-box; margin: 0; padding: 0; }
  html, body { width: 1200px; height: 769px; overflow: hidden; }
  body {
    background: var(--stage);
    font-family: "Roboto", Arial, sans-serif;
    color: var(--ink);
    position: relative;
  }
  .card {
    position: absolute;
    top: 230px;
    width: 540px;
    height: 309px;
    background: var(--card);
    border-radius: 3px;
    box-shadow: 0 6px 18px rgba(0,0,0,.35);
    overflow: hidden;
  }
  .card--front { left: 45px; }
  .card--back { left: 615px; }

  .wordmark { position: absolute; text-align: center; font-weight: 500; color: var(--ink); }
  .wordmark__name { display: block; font-size: 38px; letter-spacing: 2px; line-height: 1; }
  .wordmark__tag { display: block; font-size: 14px; letter-spacing: 3px; margin-top: 10px; }

  .card--front .wordmark { right: 28px; top: 34px; width: 250px; }
  .card--front .wordmark__name { font-size: 30px; }
  .card--front .wordmark__tag { font-size: 12px; }

  .divider {
    position: absolute; left: 0; top: 124px;
    width: 500px; height: 2px; background: var(--rule);
  }
  .address {
    position: absolute; right: 28px; top: 138px;
    text-align: right; font-size: 13px; line-height: 17px; color: var(--ink-soft);
  }
  .address__web { margin-top: 2px; }

  .person { position: absolute; left: 26px; top: 178px; }
  .person__name { font-size: 17px; font-weight: 700; letter-spacing: .3px; line-height: 19px; }
  .person__title { font-size: 13px; color: var(--ink-soft); line-height: 16px; }
  .person__rule { width: 200px; height: 1.5px; background: var(--rule); margin: 7px 0 6px; }

  .contacts { list-style: none; }
  .contacts li {
    display: flex; align-items: center; gap: 9px;
    font-size: 13px; line-height: 17px; color: var(--ink-soft);
  }
  .contacts svg { width: 12px; height: 12px; fill: var(--ink-soft); flex: none; }

  .card--back .wordmark { left: 0; right: 0; top: 98px; }
  .card--back .web {
    position: absolute; left: 0; right: 0; top: 212px;
    text-align: center; font-size: 12px; letter-spacing: 2.5px; color: var(--ink-soft);
  }
</style>
</head>
<body>

  <section class="card card--front" aria-label="Business card front">
    <div class="wordmark">
      <span class="wordmark__name">BRIGHTLINE</span>
      <span class="wordmark__tag">TATTOO REMOVAL</span>
    </div>
    <div class="divider"></div>
    <address class="address" style="font-style:normal">
      <div>4615 Oakmere Pkwy</div>
      <div>Suite 210</div>
      <div>Raleigh, NC 27654</div>
      <div class="address__web">www.brightlinetattooremoval.example</div>
    </address>

    <div class="person">
      <div class="person__name">MELISSA THORNBURY</div>
      <div class="person__title">Chief Executive Offer</div>
      <div class="person__rule"></div>
      <ul class="contacts">
        <li>
          <svg viewBox="0 0 24 24" aria-hidden="true"><path d="M6.6 10.8a15 15 0 0 0 6.6 6.6l2.2-2.2a1 1 0 0 1 1-.25 11.4 11.4 0 0 0 3.6.57 1 1 0 0 1 1 1V20a1 1 0 0 1-1 1A17 17 0 0 1 3 4a1 1 0 0 1 1-1h3.5a1 1 0 0 1 1 1c0 1.25.2 2.45.57 3.57a1 1 0 0 1-.25 1z"/></svg>
          919.362.4178
        </li>
        <li>
          <svg viewBox="0 0 24 24" aria-hidden="true"><path d="M7 1h10a2 2 0 0 1 2 2v18a2 2 0 0 1-2 2H7a2 2 0 0 1-2-2V3a2 2 0 0 1 2-2zm0 3v14h10V4zm5 15.2a1.2 1.2 0 1 0 0 2.4 1.2 1.2 0 0 0 0-2.4z"/></svg>
          919.537.2846
        </li>
        <li>
          <svg viewBox="0 0 24 24" aria-hidden="true"><path d="M6 2h9l3 3v4H6zm-3 8h18a2 2 0 0 1 2 2v7H1v-7a2 2 0 0 1 2-2zm3 6v6h12v-6z"/></svg>
          919.685.3907
        </li>
        <li>
          <svg viewBox="0 0 24 24" aria-hidden="true"><path d="M2 5h20v14H2zm2 2v.5l8 5.5 8-5.5V7zm0 3v7h16v-7l-8 5.5z"/></svg>
          mthornbury@brightlinetattooremoval.example
        </li>
      </ul>
    </div>
  </section>

  <section class="card card--back" aria-label="Business card back">
    <div class="wordmark">
      <span class="wordmark__name">BRIGHTLINE</span>
      <span class="wordmark__tag">TATTOO REMOVAL</span>
    </div>
    <div class="web">www.brightlinetattooremoval.example</div>
  </section>

</body>
</html>
```